Satchel & Sundial needs new business card design

I need a new business card design. I'm looking for out-of-the-box design which represents the freedom of being a location independent entrepreneur.
I offer coaching, retreats and trips.
I would like to see designs with and without the photo.
Colors I use are black (#000000), green (#25A796) and brown (#D7C38C)
Website satchelandsundial.example

Target Market(s)

location independent entrepreneurs, digital nomads, people looking to swap the 9 to 5 for a lifestyle business

Industry/Entity Type

Business

Contact Information for Business Card

Dorota Falkner
Your Lifestyle Business Coach, Retreat & Trip Leader
http://satchelandsundial.example
hello@satchelandsundial.example
Live a life you don't need a holiday from

Font styles to use
Serif
Sans Serif

Requirements
Must have
• One side should contain only the logo. I would also consider having the "Live a life you don't need a holiday from" on that side too (depending on how it looks)
• Please show both sides on the designs.

```html
<!DOCTYPE html>
<html lang="en">
<head>
<meta charset="utf-8">
<title>Satchel &amp; Sundial — Business Card</title>
<link href="https://fonts.googleapis.com/css2?family=Source+Sans+3:wght@400;600;700&display=swap" rel="stylesheet">
<style>
  :root {
    --stage: #121212;
    --brand-green: #25a796;
    --ink: #1b1b1b;
    --paper-white: #ffffff;
    --silver-light: #fbfbfb;
    --silver-mid: #e6e5e6;
    --silver-dark: #d2d1d3;
  }
  * { margin: 0; padding: 0; box-sizing: border-box; }
  html, body {
    width: 1200px;
    height: 900px;
    overflow: hidden;
    background: var(--stage);
    font-family: "Source Sans 3", "Myriad Pro", sans-serif;
  }
  .stage { position: relative; width: 1200px; height: 900px; }

  .card {
    position: absolute;
    top: 271px;
    width: 457px;
    height: 282px;
    border-radius: 14px;
    overflow: hidden;
  }
  .card--front { left: 137px; background: var(--brand-green); }
  .card--back {
    left: 626px;
    background:
      radial-gradient(ellipse 260px 170px at 78% 12%, var(--silver-light) 0%, rgba(251,251,251,0) 100%),
      linear-gradient(200deg, var(--silver-mid) 0%, var(--silver-mid) 45%, var(--silver-dark) 100%);
  }

  .wordmark {
    position: absolute;
    color: var(--ink);
    font-weight: 700;
    letter-spacing: 0.5px;
    white-space: nowrap;
  }
  .card--front .wordmark { left: 24px; top: 22px; font-size: 38px; line-height: 1; }
  .card--back .wordmark {
    left: 0; right: 0; top: 112px;
    text-align: center; font-size: 44px; line-height: 1;
  }

  .tagline {
    position: absolute;
    left: 24px; top: 125px;
    color: var(--paper-white);
    font-size: 13px;
    font-weight: 400;
    text-transform: uppercase;
    letter-spacing: 0.1px;
  }

  .holder-name {
    position: absolute;
    left: 25px; top: 192px;
    color: var(--ink);
    font-size: 17px;
    font-weight: 600;
  }

  .holder-roles, .contact-list {
    position: absolute;
    top: 222px;
    list-style: none;
    color: var(--paper-white);
    font-size: 13px;
    line-height: 17px;
  }
  .holder-roles { left: 25px; }
  .contact-list { right: 26px; text-align: right; }
  .contact-list li { display: flex; justify-content: flex-end; align-items: center; gap: 5px; }
  .contact-icon { width: 9px; height: 9px; flex: none; }
</style>
</head>
<body>
<main class="stage">

  <section class="card card--front" aria-label="Business card front">
    <div class="wordmark">Satchel &amp; Sundial</div>
    <p class="tagline">Live a life you don't need a holiday from</p>
    <h1 class="holder-name">Dorota Falkner</h1>
    <ul class="holder-roles">
      <li>Your Lifestyle Business Coach</li>
      <li>Retreat &amp; Trip Leader</li>
    </ul>
    <ul class="contact-list">
      <li>hello@satchelandsundial.example
        <svg class="contact-icon" viewBox="0 0 10 10" aria-hidden="true">
          <rect x="0.5" y="2" width="9" height="6.5" fill="var(--ink)"/>
          <polyline points="0.8,2.4 5,5.6 9.2,2.4" fill="none" stroke="var(--brand-green)" stroke-width="0.9"/>
        </svg>
      </li>
      <li>www.satchelandsundial.example
        <svg class="contact-icon" viewBox="0 0 10 10" aria-hidden="true">
          <circle cx="5" cy="5" r="4.6" fill="var(--ink)"/>
          <ellipse cx="5" cy="5" rx="1.8" ry="4.2" fill="none" stroke="var(--brand-green)" stroke-width="0.7"/>
          <line x1="0.8" y1="5" x2="9.2" y2="5" stroke="var(--brand-green)" stroke-width="0.7"/>
        </svg>
      </li>
    </ul>
  </section>

  <section class="card card--back" aria-label="Business card back">
    <div class="wordmark">Satchel &amp; Sundial</div>
  </section>

</main>
</body>
</html>
```